Professional Single Page Website Design for Tollbrook Advisory

Tollbrook Advisory is a new business consultancy specializing in providing expert services to small businesses, primarily in the brick-and-mortar retail and food service sectors. We offer a range of services including franchise development and launch, due diligence, and construction management.

Currently, we have a basic website set up at www.tollbrookadvisory.example, but we need a professional touch to enhance its design and functionality.

Project Requirements:
- Single Page Design: For now, we need a single page design that effectively showcases who we are, our services, and contact information.
- Future Expansion: The design should be flexible and scalable for future expansion to include additional pages like specific service offerings, about us, and a dedicated contact page.
- Design Aesthetic: We are looking for a modern yet professional design that aligns with our brand identity.
- Logo: We have a logo that we like, which was also sourced from Pixel Bazaar. The logo files are attached to this project brief.

Key Sections to Include:
- Hero Section: An engaging introduction to Tollbrook Advisory with a strong visual impact.
- About Us: A brief overview of who we are and our mission.
- Team: Section for the profiles of the two principals.
- Services: A clear and concise presentation of our services, including franchise development, due diligence, and construction management.
- Contact Information: Easy-to-find contact details, including a form for inquiries.
- Call to Action: Encouraging visitors to get in touch with us for consultations or further information.

Design Considerations:
- Ensure the design is responsive and mobile-friendly.
- Include high-quality images and icons that complement our services and industry.
- We do not need development services, this is only a design project.

```html
<!DOCTYPE html>
<html lang="en">
<head>
<meta charset="utf-8">
<title>Tollbrook Advisory</title>
<link href="https://fonts.googleapis.com/css2?family=Poppins:wght@400;500;600&display=swap" rel="stylesheet">
<style>
:root{
  --green:#8fc4aa;
  --green-soft:#a9d3bf;
  --green-band:#97c6af;
  --dark:#1f2a33;
  --ink:#1d1d1d;
  --muted:#444;
  --grey-bg:#f5f5f5;
  --white:#fff;
}
*{box-sizing:border-box;margin:0;padding:0}
html,body{width:1200px;height:3415px;overflow:hidden}
body{font-family:'Poppins',sans-serif;color:var(--ink);position:relative;background:var(--white)}
.abs{position:absolute}
.btn{position:absolute;background:var(--green);color:var(--dark);font-size:13px;font-weight:500;display:flex;align-items:center;justify-content:center;border-radius:2px}
.accent{color:var(--green)}
/* hero */
.hero{left:0;top:0;width:1200px;height:565px;background:#0b0b0b}
.hero-photo{left:700px;top:0;width:500px;height:565px;background:linear-gradient(90deg,#0b0b0b 0%,#3a3530 30%,#b46a2a 55%,#d98a2e 70%,#6a6a64 100%)}
.brand{display:flex;align-items:center;gap:10px;color:var(--white);font-size:20px;font-weight:500}
.brand-dot{width:44px;height:44px;border-radius:50%;background:var(--green)}
.nav{top:42px;left:563px;display:flex;gap:52px;font-size:13px;color:var(--white)}
.nav .on{color:var(--green)}
.hero-title{left:142px;top:140px;width:500px;font-size:34px;font-weight:500;line-height:1.25;color:var(--white)}
.hero-sub{left:142px;top:230px;width:480px;font-size:24px;font-weight:400;line-height:1.25;color:var(--white)}
.hero-txt{left:142px;top:298px;width:470px;font-size:13.5px;line-height:1.5;color:#e6e6e6}
/* about */
.about-img{left:175px;top:660px;width:322px;height:322px;transform:rotate(45deg);border-radius:90px;background:linear-gradient(135deg,#c98a72,#e9e6e2 55%,#8b8f93)}
.h-sec{font-size:33px;font-weight:500}
.about-title{left:580px;top:632px}
.about-txt{left:580px;top:685px;width:478px;font-size:11.6px;line-height:1.65;color:var(--muted)}
.about-txt p{margin-bottom:9px}
/* services */
.services-bg{left:0;top:1100px;width:1200px;height:816px;background:var(--grey-bg)}
.center{left:0;width:1200px;text-align:center}
.tabs{left:142px;top:1221px;width:916px;height:146px;display:flex}
.tab{flex:1;display:flex;flex-direction:column;align-items:center;justify-content:flex-end;padding-bottom:30px;font-size:13px;font-weight:500;text-align:center;line-height:1.25;gap:22px}
.tab.on{background:var(--dark);color:var(--white);flex:0 0 168px}
.tab svg{width:52px;height:48px}
.svc-title{left:142px;top:1413px;font-size:24px;font-weight:500;color:var(--green)}
.svc-txt{left:142px;top:1452px;width:425px;font-size:11.6px;line-height:1.65;color:var(--muted)}
.svc-txt p{margin-bottom:10px}
.svc-img{left:671px;top:1411px;width:387px;height:302px;background:radial-gradient(circle at 50% 50%,#f2f2f2,#dcdcdc);border-radius:3px}
.arrow{width:36px;height:36px;border-radius:50%}
/* cta */
.cta-panel{left:142px;top:1789px;width:916px;height:268px;border-radius:4px;background:linear-gradient(180deg,#4e5e6a 0%,#3a4f5e 50%,#2b4253 100%)}
.cta-title{left:0;width:1200px;top:1832px;text-align:center;font-size:34px;font-weight:600;line-height:1.2;color:var(--white)}
.cta-txt{top:1885px;left:260px;width:680px;text-align:center;font-size:15px;line-height:1.6;color:#eef2f5}
/* team */
.card{border:1px solid #e6e6e6;border-radius:6px;background:var(--white)}
.photo{width:120px;height:120px;border-radius:4px}
.name{font-size:22px;color:var(--green)}
.role{font-size:15px;font-weight:500}
.bio{font-size:11.6px;line-height:1.75;color:var(--muted)}
/* contact */
.map{left:0;top:2617px;width:600px;height:423px;background:linear-gradient(135deg,#e9ecef,#dfe6e3 50%,#e6e9ee)}
.contact{left:600px;top:2617px;width:600px;height:423px;background:var(--green-band)}
.field{position:absolute;left:670px;width:388px;height:42px;background:var(--green-soft);display:flex;align-items:center;gap:10px;padding-left:14px;font-size:11.5px;color:#2a3a33}
.field svg{width:14px;height:14px}
.submit{left:670px;top:2942px;width:388px;height:40px;background:var(--dark);color:var(--white);font-size:13px;font-weight:500;display:flex;align-items:center;justify-content:center}
/* footer */
.footer{left:0;top:3040px;width:1200px;height:335px;background:var(--dark);color:var(--white)}
.f-head{font-size:15px;font-weight:500;color:var(--white)}
.f-item{display:flex;align-items:center;gap:12px;font-size:13px;color:var(--white);line-height:1.5}
.f-icon{width:38px;height:38px;border-radius:50%;background:#34414c;flex:0 0 38px;display:flex;align-items:center;justify-content:center}
.f-icon svg{width:15px;height:15px}
.s-icon{width:34px;height:34px;flex-basis:34px;border:1px solid #4a5863;background:none}
.copy{left:0;top:3375px;width:1200px;height:40px;background:var(--green);font-size:14px;display:flex;align-items:center;justify-content:center;color:var(--dark)}
</style>
</head>
<body>

<!-- Hero -->
<section class="abs hero">
  <div class="abs hero-photo" role="img" aria-label="Smiling professional in an orange sweater holding a tablet in an office"></div>
  <div class="abs brand" style="left:142px;top:28px"><span class="brand-dot"></span>Tollbrook Advisory</div>
  <nav class="abs nav"><span class="on">Home</span><span>About Us</span><span>Services</span><span>Team</span></nav>
  <div class="btn" style="left:953px;top:34px;width:105px;height:34px">Contact Us</div>
  <h1 class="abs hero-title">Building Success in Southern California</h1>
  <h2 class="abs hero-sub">Expertise at Every Step: From Planning to Execution</h2>
  <p class="abs hero-txt">At Tollbrook, we blend innovative strategies with local market expertise to guide your commercial real estate ventures. Whether you're launching a new restaurant, investing in retail spaces, or expanding a franchise, our dedicated team is here to turn your real estate aspirations into tangible success. Dive into a partnership that grows with you.</p>
  <div class="btn" style="left:142px;top:438px;width:105px;height:33px">Learn More</div>
</section>

<!-- About -->
<section>
  <div class="abs about-img" role="img" aria-label="Modern brick storefront with glass doors"></div>
  <h2 class="abs h-sec about-title">About Tollbrook <span class="accent">Advisory</span></h2>
  <div class="abs about-txt">
    <p>Welcome to Tollbrook Advisory, your trusted partner in navigating the complexities of the real estate and small business markets. Founded by industry veterans Ruben Castillo and Daniel Hwang, we specialize in providing comprehensive services tailored to the unique needs of our clients. Whether you're a franchisee, a new restaurant owner, or a commercial real estate investor, our expertise in due diligence, construction management, and investment property evaluation ensures you make informed, strategic decisions.</p>
    <p>At Tollbrook Advisory, we are committed to your success. Our approach combines meticulous analysis, strategic insights, &amp; personalized service to help you achieve your business goals. We pride ourselves on our ability to deliver results that exceed expectations, fostering long-term relationships built on trust &amp; excellence.</p>
    <p>Discover how Tollbrook Advisory can support your business journey. Partner with us and experience the difference our dedication and expertise can make.</p>
  </div>
  <div class="btn" style="left:580px;top:965px;width:106px;height:35px">Contact Us</div>
</section>

<!-- Services -->
<section>
  <div class="abs services-bg"></div>
  <h2 class="abs center h-sec" style="top:1160px">Tollbrook <span class="accent">Services</span></h2>
  <div class="abs tabs">
    <div class="tab on"><svg viewBox="0 0 52 48" fill="none" stroke="var(--green)" stroke-width="2"><rect x="6" y="18" width="32" height="24"/><path d="M4 18h36l-4-10H8z"/><rect x="12" y="26" width="8" height="16"/><path d="M44 8v30M40 12l4-4 4 4M40 34l4 4 4-4"/></svg>Franchise Development<br>&amp; Launch</div>
    <div class="tab"><svg viewBox="0 0 52 48" fill="none" stroke="var(--green)" stroke-width="2"><circle cx="20" cy="20" r="10"/><circle cx="30" cy="28" r="9"/><path d="M37 35l9 9"/></svg>Due Diligence<br>Services</div>
    <div class="tab"><svg viewBox="0 0 52 48" fill="none" stroke="var(--green)" stroke-width="2"><circle cx="26" cy="16" r="8"/><circle cx="26" cy="16" r="3"/><path d="M6 38c8-6 14-6 20-4h10M6 44h28l12-8"/></svg>Building &amp; Construction<br>Management</div>
    <div class="tab"><svg viewBox="0 0 52 48" fill="none" stroke="var(--green)" stroke-width="2"><path d="M12 20L26 8l14 12v14H12z"/><circle cx="26" cy="24" r="6"/><path d="M6 40c8-5 14-5 20-3h12l8-6"/></svg>Investment Property<br>Evaluation</div>
    <div class="tab"><svg viewBox="0 0 52 48" fill="none" stroke="var(--green)" stroke-width="2"><circle cx="26" cy="20" r="14"/><path d="M20 26V20M26 26V14M32 26V18"/><path d="M14 38l-6 6M34 36l10 6"/></svg>Market Analysis &amp;<br>Feasibility Studies</div>
  </div>
  <h3 class="abs svc-title">Franchise Development &amp; Launch</h3>
  <div class="abs svc-txt">
    <p>At Tollbrook Advisory, our Franchise Development &amp; Launch service is designed to transform your successful business into a thriving franchise. We start by thoroughly evaluating your business model to determine its franchisability. Once confirmed, our team handles every aspect of the franchise setup, including legal documentation, branding, marketing strategies, operational guidelines, and franchisee recruitment.</p>
    <p>Our goal is to ensure a seamless and efficient transition from a single successful location to a robust franchise network, empowering your business to scale effectively and achieve exponential growth. Partner with us to turn your business into a nationwide brand.</p>
  </div>
  <div class="btn" style="left:142px;top:1669px;width:106px;height:34px">Contact Us</div>
  <div class="abs svc-img" role="img" aria-label="Coloured pushpins connected by red thread on a white surface"></div>
  <svg class="abs arrow" style="left:84px;top:1544px" viewBox="0 0 36 36"><circle cx="18" cy="18" r="17" fill="#fff" stroke="var(--dark)" stroke-width="1.5"/><path d="M25 18H11M16 13l-5 5 5 5" fill="none" stroke="var(--dark)" stroke-width="1.8"/></svg>
  <svg class="abs arrow" style="left:1079px;top:1544px" viewBox="0 0 36 36"><circle cx="18" cy="18" r="18" fill="var(--dark)"/><path d="M11 18h14M20 13l5 5-5 5" fill="none" stroke="#fff" stroke-width="1.8"/></svg>
</section>

<!-- Call to action -->
<section>
  <div class="abs cta-panel" role="img" aria-label="Aerial view of a commercial office park with trees"></div>
  <h2 class="abs cta-title">Unlock Your Business <span class="accent">Potential Today!</span></h2>
  <p class="abs cta-txt">At Tollbrook Advisory, we're dedicated to turning your business aspirations into reality. Our expertise and commitment ensure you make informed, strategic decisions that drive success. Take the first step towards achieving your goals with confidence.</p>
  <div class="btn" style="left:533px;top:1968px;width:134px;height:33px">Get Started Now</div>
</section>

<!-- Team -->
<section>
  <h2 class="abs center h-sec" style="top:2132px;font-size:37px">Our Leadership <span class="accent">Team</span></h2>

  <div class="abs card" style="left:183px;top:2244px;width:402px;height:225px"></div>
  <div class="abs photo" style="left:142px;top:2205px;background:linear-gradient(160deg,#3c3a38,#6b5a4c)" role="img" aria-label="Portrait of Daniel Hwang"></div>
  <div class="abs name" style="left:284px;top:2265px">Daniel Hwang</div>
  <div class="abs role" style="left:285px;top:2298px">Principal</div>
  <p class="abs bio" style="left:202px;top:2340px;width:365px">Daniel Hwang is a seasoned real estate expert with extensive experience in project and construction management, and a licensed real estate agent in California. Fluent in both English and Korean, he specializes in commercial real estate, bringing invaluable expertise to Tollbrook Advisory...</p>

  <div class="abs card" style="left:656px;top:2244px;width:402px;height:225px"></div>
  <div class="abs photo" style="left:614px;top:2205px;background:linear-gradient(160deg,#9fb9cf,#e8ecef 60%,#b8a99a)" role="img" aria-label="Portrait of Ruben Castillo"></div>
  <div class="abs name" style="left:757px;top:2265px">Ruben Castillo</div>
  <div class="abs role" style="left:758px;top:2298px">Principal</div>
  <p class="abs bio" style="left:675px;top:2340px;width:370px">Ruben Castillo brings almost 20 years of rich experience as a real estate investor and a pivotal role at one of southern California's largest real estate management firms, where he led sales and marketing strategies to elevate property value and investor returns. His vast expertise spans...</p>

  <div class="btn" style="left:547px;top:2498px;width:106px;height:34px">Contact Us</div>
</section>

<!-- Contact -->
<section>
  <div class="abs map" role="img" aria-label="Street map showing the office location"></div>
  <div class="abs contact"></div>
  <h2 class="abs h-sec" style="left:670px;top:2664px">Contact <span style="color:var(--white)">Us</span></h2>
  <div class="field" style="top:2725px"><svg viewBox="0 0 14 14" fill="none" stroke="#2a3a33" stroke-width="1.2"><circle cx="7" cy="4.5" r="3"/><path d="M1.5 13c1-3 3-4 5.5-4s4.5 1 5.5 4"/></svg>Your Name*</div>
  <div class="field" style="top:2779px"><svg viewBox="0 0 14 14" fill="none" stroke="#2a3a33" stroke-width="1.2"><rect x="1" y="3" width="12" height="8"/><path d="M1 3l6 5 6-5"/></svg>Your Email*</div>
  <div class="field" style="top:2833px"><svg viewBox="0 0 14 14" fill="none" stroke="#2a3a33" stroke-width="1.2"><path d="M3 1l2 3-1.5 1.5a8 8 0 005 5L10 9l3 2-1 2C6 13 1 8 1 2z"/></svg>Your Phone*</div>
  <div class="field" style="top:2888px"><svg viewBox="0 0 14 14" fill="none" stroke="#2a3a33" stroke-width="1.2"><circle cx="7" cy="3" r="2"/><path d="M5 6h4v7H5z"/></svg>Additional Information</div>
  <div class="abs submit">Submit Now</div>
</section>

<!-- Footer -->
<footer>
  <div class="abs footer"></div>
  <div class="abs f-head" style="left:142px;top:3096px">Contact Details</div>
  <div class="abs f-item" style="left:142px;top:3142px"><span class="f-icon"><svg viewBox="0 0 15 15" fill="var(--green)"><path d="M7.5 0a5 5 0 015 5c0 4-5 10-5 10S2.5 9 2.5 5a5 5 0 015-5z"/><circle cx="7.5" cy="5" r="1.8" fill="#34414c"/></svg></span><span>410 Harbor View Dr Suite 200<br>Lakeport, CA 90412, USA</span></div>
  <div class="abs f-item" style="left:142px;top:3210px"><span class="f-icon"><svg viewBox="0 0 15 15" fill="var(--green)"><path d="M3 1l2.5 3-1.5 2a8 8 0 005 5l2-1.5 3 2.5-1.5 2C6 14 1 9 1 3z"/></svg></span><span>Phone<br>555 010 2468</span></div>
  <div class="abs f-item" style="left:142px;top:3278px"><span class="f-icon"><svg viewBox="0 0 15 15" fill="none" stroke="var(--green)" stroke-width="1.4"><rect x="1" y="3" width="13" height="9"/><path d="M1 3l6.5 5L14 3"/></svg></span><span>Email<br>info@tollbrookadvisory.example</span></div>

  <div class="abs f-head" style="left:557px;top:3096px">Follow Us</div>
  <div class="abs f-item" style="left:557px;top:3138px"><span class="f-icon s-icon"></span>Community</div>
  <div class="abs f-item" style="left:557px;top:3185px"><span class="f-icon s-icon"></span>Gallery</div>
  <div class="abs f-item" style="left:557px;top:3232px"><span class="f-icon s-icon"></span>Updates</div>
  <div class="abs f-item" style="left:557px;top:3279px"><span class="f-icon s-icon"></span>Videos</div>

  <div class="abs" style="left:898px;top:3128px;width:118px;height:118px;border-radius:50%;background:var(--green)"></div>
  <div class="abs" style="left:820px;top:3258px;width:270px;text-align:center;font-size:23px;font-weight:500;color:var(--white)">Tollbrook Advisory</div>
</footer>

<div class="abs copy">©2024 Tollbrook Advisory. All Rights Reserved.</div>

</body>
</html>
```